i would like a business card to leave with customers and potential customers for electrical work and for the supply and install of reverse cycle airconditioning in the domestic and commercial market.
I own my own business and im a sole trader. I have an a'class electrical lisence and also a refrigeration lisence so i am
able to offer complete installations in airconditioning by a fully qualified and lisenced tradesman.
im looking for something that comes across as unique and professional.
i had the coluor black and some gold in mind but open to any coluors.
something like Lanterra Electrical & Refrigeration
or Lanterra Air.
i will use this design on a business card to advertise through summer to help generate installs through the busy season.

Target Market(s)

Mainly domestic house holds through summer who are in need of airconditioning and reliable information to acomadate thier cooling and heating requirements

Industry/Entity Type

Electrical

Requirements
Must have
• Business name- Lanterra
My name- Mark Delford
My mobile no- 0438 517 290
My email- mrdelford@qelvo.com.au
Installation & Decomissioning of aiconditioning split systems
LIC NO: TRK 540316
Nice to have
• Lanterra Electrical & Refrigeration

```html
<!DOCTYPE html>
<html lang="en">
<head>
<meta charset="utf-8">
<title>Lanterra Electrical &amp; Refrigeration – Business Cards</title>
<link rel="stylesheet" href="https://fonts.googleapis.com/css2?family=Exo+2:wght@400;800&family=Arimo:wght@400;700&display=swap">
<style>
  :root {
    --red: #e3212b;
    --red-deep: #c8141d;
    --white: #ffffff;
    --paper: #f4f4f4;
    --ink: #2b2b2b;
    --grey: #555555;
    --ghost: #e6e6e6;
    --stage: #3a3a3a;
    --badge-blue: #2a8fd0;
    --badge-green: #7dc242;
  }
  * { box-sizing: border-box; margin: 0; padding: 0; }
  html, body { width: 1200px; height: 874px; overflow: hidden; }
  body { background: var(--stage); position: relative; font-family: "Arimo", Arial, sans-serif; }

  .card {
    position: absolute;
    width: 520px;
    height: 318px;
    overflow: hidden;
    box-shadow: 0 10px 28px rgba(0,0,0,.45);
  }
  .card--back { left: 340px; top: 60px; background: var(--white); }
  .card--front-light { left: 60px; top: 470px; background: var(--white); }
  .card--front-red { left: 620px; top: 470px; background: var(--red); }

  /* brand lockup */
  .brand { position: absolute; display: flex; align-items: center; }
  .brand__mark { border-radius: 50%; flex: none; }
  .brand__text { display: flex; flex-direction: column; }
  .brand__name {
    font-family: "Exo 2", Arial, sans-serif;
    font-weight: 800;
    letter-spacing: .02em;
    line-height: .95;
    text-transform: uppercase;
  }
  .brand__tag {
    font-family: "Arimo", Arial, sans-serif;
    font-weight: 400;
    letter-spacing: .01em;
  }

  /* back card */
  .band-top { position: absolute; left: 0; top: 0; width: 100%; height: 26px; background: var(--red); }
  .band-bottom {
    position: absolute; left: 0; bottom: 0; width: 100%; height: 44px;
    background: var(--red);
    display: flex; align-items: center; justify-content: flex-end;
    padding-right: 24px;
  }
  .band-bottom__text { color: var(--white); font-size: 15px; letter-spacing: .01em; }
  .ghost-circle {
    position: absolute; left: 150px; top: 58px; width: 200px; height: 200px;
    border-radius: 50%; border: 14px solid var(--ghost);
  }
  .card--back .brand { left: 28px; top: 52px; gap: 12px; }
  .card--back .brand__mark { width: 60px; height: 60px; border: 6px solid var(--red); }
  .card--back .brand__name { color: var(--red); font-size: 40px; }
  .card--back .brand__tag { color: var(--ink); font-size: 13px; margin-top: 2px; }

  .contact { position: absolute; right: 30px; top: 118px; width: 220px; }
  .contact__name { color: var(--red); font-size: 20px; font-weight: 700; margin-bottom: 6px; }
  .contact__line { color: var(--grey); font-size: 13.5px; line-height: 1.35; }

  .partner-badge {
    position: absolute; left: 26px; bottom: 56px; width: 46px; height: 46px;
    background: linear-gradient(135deg, var(--badge-blue) 50%, var(--badge-green) 50%);
  }

  /* fronts */
  .card--front-light .brand,
  .card--front-red .brand {
    left: 0; top: 0; width: 100%; height: 100%;
    flex-direction: column; justify-content: center; gap: 18px;
  }
  .card--front-light .brand__mark,
  .card--front-red .brand__mark { width: 120px; height: 120px; }
  .card--front-light .brand__mark { border: 10px solid var(--red); }
  .card--front-red .brand__mark { border: 10px solid var(--white); }
  .card--front-light .brand__text,
  .card--front-red .brand__text { align-items: flex-end; }
  .card--front-light .brand__name,
  .card--front-red .brand__name { font-size: 46px; }
  .card--front-light .brand__tag,
  .card--front-red .brand__tag { font-size: 15px; margin-top: 2px; }
  .card--front-light .brand__name { color: var(--red); }
  .card--front-light .brand__tag { color: var(--ink); }
  .card--front-red .brand__name,
  .card--front-red .brand__tag { color: var(--white); }
</style>
</head>
<body>

  <section class="card card--back" aria-label="Business card, contact side">
    <div class="band-top"></div>
    <div class="ghost-circle" aria-hidden="true"></div>
    <div class="brand">
      <span class="brand__mark" aria-hidden="true"></span>
      <div class="brand__text">
        <span class="brand__name">Lanterra</span>
        <span class="brand__tag">Electrical &amp; Refrigeration</span>
      </div>
    </div>
    <div class="contact">
      <p class="contact__name">Mark Delford</p>
      <p class="contact__line">M: 0438 517 290</p>
      <p class="contact__line">E: mrdelford@qelvo.com.au</p>
      <p class="contact__line">LIC NO: TRK 540316</p>
    </div>
    <div class="partner-badge" role="img" aria-label="Partner accreditation badge"></div>
    <div class="band-bottom">
      <p class="band-bottom__text">Installation &amp; Decomissioning of airconditioning split systems</p>
    </div>
  </section>

  <section class="card card--front-light" aria-label="Business card, white logo side">
    <div class="brand">
      <span class="brand__mark" aria-hidden="true"></span>
      <div class="brand__text">
        <span class="brand__name">Lanterra</span>
        <span class="brand__tag">Electrical &amp; Refrigeration</span>
      </div>
    </div>
  </section>

  <section class="card card--front-red" aria-label="Business card, red logo side">
    <div class="brand">
      <span class="brand__mark" aria-hidden="true"></span>
      <div class="brand__text">
        <span class="brand__name">Lanterra</span>
        <span class="brand__tag">Electrical &amp; Refrigeration</span>
      </div>
    </div>
  </section>

</body>
</html>
```